MRT Property - Business Cards

Looking for a business card & general letterhead, signage etc design for our new logo.

Colours:
000a20
0056a2
00b5ef
0088ce
68cef2

Fonts:
Poppins
Karla

Please keep look and feel of new brand - example in the zip package I sent.

```html
<!DOCTYPE html>
<html lang="en">
<head>
<meta charset="utf-8">
<title>MRT Property – Business Cards</title>
<link href="https://fonts.googleapis.com/css2?family=Poppins:wght@400;500;600;700&family=Karla:wght@400;500&display=swap" rel="stylesheet">
<style>
  :root {
    --ink: #000a20;
    --navy: #1a1f38;
    --navy-deep: #121629;
    --royal: #0056a2;
    --cyan: #00b5ef;
    --mid: #0088ce;
    --sky: #68cef2;
    --paper: #f7f8fa;
    --grey: #4a4d55;
    --stage: #1b1b1d;
  }
  * { box-sizing: border-box; margin: 0; padding: 0; }
  html, body { width: 1200px; height: 852px; overflow: hidden; }
  body {
    background: var(--stage);
    font-family: "Poppins", sans-serif;
    position: relative;
  }
  .card {
    position: absolute;
    top: 283px;
    width: 500px;
    height: 286px;
    border-radius: 18px;
    overflow: hidden;
  }
  /* Back of card */
  .card-back {
    left: 80px;
    background: linear-gradient(135deg, var(--navy) 0%, var(--navy-deep) 100%);
  }
  .card-back .wordmark {
    position: absolute;
    left: 0; right: 0; top: 92px;
    text-align: center;
    font-weight: 700;
    font-size: 44px;
    letter-spacing: 1px;
    color: var(--cyan);
  }
  .card-back .web {
    position: absolute;
    left: 0; right: 0; top: 226px;
    text-align: center;
    font-family: "Karla", sans-serif;
    font-size: 11px;
    letter-spacing: 6px;
    color: #c9cfdc;
  }
  .card-back .rule {
    position: absolute;
    left: 24px; right: 24px; bottom: 22px;
    height: 3px;
    background: linear-gradient(90deg, var(--cyan) 0%, var(--mid) 50%, var(--royal) 100%);
  }
  /* Front of card */
  .card-front {
    left: 620px;
    background: var(--paper);
  }
  .brand-block {
    position: absolute;
    left: 36px; top: 62px;
    width: 170px; height: 170px;
    background: var(--mid);
  }
  .card-front .wordmark {
    position: absolute;
    right: 28px; top: 30px;
    font-weight: 700;
    font-size: 28px;
    color: var(--royal);
    text-align: right;
  }
  .person {
    position: absolute;
    right: 28px; top: 104px;
    text-align: right;
  }
  .person .name {
    font-weight: 600;
    font-size: 19px;
    color: var(--mid);
    line-height: 1.1;
  }
  .person .role {
    font-family: "Karla", sans-serif;
    font-size: 11px;
    color: var(--grey);
  }
  .contacts {
    position: absolute;
    right: 28px; top: 168px;
    list-style: none;
    text-align: right;
  }
  .contacts li {
    font-family: "Karla", sans-serif;
    font-size: 13px;
    color: var(--grey);
    line-height: 22px;
    display: flex;
    justify-content: flex-end;
    align-items: center;
    gap: 8px;
  }
  .contacts svg { width: 13px; height: 13px; fill: var(--mid); }
</style>
</head>
<body>
  <section class="card card-back" aria-label="Business card back">
    <div class="wordmark">MRT Property</div>
    <div class="web">www.mrtproperty.com</div>
    <div class="rule"></div>
  </section>

  <section class="card card-front" aria-label="Business card front">
    <div class="brand-block" role="img" aria-label="Large brand mark area"></div>
    <div class="wordmark">MRT Property</div>
    <div class="person">
      <div class="name">Daniel Hale</div>
      <div class="role">Managing Director</div>
    </div>
    <ul class="contacts">
      <li>555-010-2040
        <svg viewBox="0 0 16 16" aria-hidden="true"><path d="M3.6 1.5l2.3 2.6-1.3 1.7c.9 2 2.4 3.5 4.5 4.6l1.7-1.3 2.6 2.3-1.3 2.6C7 13.8 2.2 9 1.2 2.8z"/></svg>
      </li>
      <li>daniel@mrtproperty.com
        <svg viewBox="0 0 16 16" aria-hidden="true"><path d="M1 3h14v10H1z M2 4.2v.4l6 4 6-4v-.4z" fill-rule="evenodd"/></svg>
      </li>
      <li>www.mrtproperty.com
        <svg viewBox="0 0 16 16" aria-hidden="true"><circle cx="8" cy="8" r="7"/><path d="M1 8h14M8 1c2.5 3 2.5 11 0 14M8 1c-2.5 3-2.5 11 0 14" stroke="#f7f8fa" stroke-width="1" fill="none"/></svg>
      </li>
    </ul>
  </section>
</body>
</html>
```